VELQUINT

1. My company will allow people to buy either stock made or custom scented aromatherapy candles, lotions,soaps,body sprays, and wax melts. As there isn't a company that allows for custom oil scent mixes but me. We are just starting with the candles and the other items will be coming later.

2. My target audience is anyone who would want to buy my product. It isn't really limited due to the nature of the product I will be providing.

3. velquint.com is the domain name (purchased from plorvex.com).

4. So what I really need is the shopping cart function. A fully coded shopping cart that will calculate shipping and sales tax if need be. I need the cart function to be just like every other major retailers shopping cart function. So they can click on an item they want and have it go into a shopping cart for the customer to then be able to go and pay for their goods. I also need help creating single pages for each product. So that each thing we make has a separate page with a description and an add to cart button.

5. I would like the color scheme to follow the logo I made. I would also like the logo top center of first page. I would like the quote " elevate your choices in aromatherapy products"

^. I basically need a checkout just like every other good website. A clear shipping area for them to populate, sales tax calculator, ya know everything a normal checkout has like tressly or dunvexa.com. I also have a vonk account already as well.

```html
<!DOCTYPE html>
<html lang="en">
<head>
<meta charset="utf-8">
<title>VELQUINT — Aromatherapy Candles</title>
<link href="https://fonts.googleapis.com/css2?family=Righteous&family=Josefin+Sans:wght@400;600;700&family=Lato:wght@400;700&display=swap" rel="stylesheet">
<style>
:root{
  --purple:#6b2fbf;
  --ink:#1d1d1d;
  --text:#444;
  --lavender:#ecdcf7;
  --lavender-soft:#efe3f8;
  --grey-band:#eeeeef;
  --white:#fff;
}
*{box-sizing:border-box;margin:0;padding:0}
html,body{width:1200px;height:4695px;overflow:hidden}
body{position:relative;font-family:"Lato",sans-serif;color:var(--ink);background:var(--white)}
.abs{position:absolute}
.photo{position:absolute}
.btn{position:absolute;display:flex;align-items:center;justify-content:center;background:var(--purple);color:#fff;border-radius:30px;font-family:"Lato",sans-serif;font-weight:700;font-size:15px;letter-spacing:.2px}
.hd{font-family:"Josefin Sans",sans-serif}
.hl{color:var(--purple);font-weight:700}

/* hero */
.hero{left:0;top:0;width:1200px;height:690px;
  background:
    radial-gradient(ellipse 260px 200px at 880px 360px,rgba(160,120,230,.75),rgba(160,120,230,0)),
    radial-gradient(ellipse 320px 180px at 640px 470px,rgba(90,50,140,.7),rgba(90,50,140,0)),
    radial-gradient(ellipse 200px 160px at 1120px 460px,rgba(225,220,215,.8),rgba(225,220,215,0)),
    linear-gradient(180deg,#a387c9 0%,#b49ad3 40%,#9c82c0 62%,#8d6f8f 74%,#b9977f 82%,#d1b49c 92%,#e0cbb7 100%);}
.nav{left:110px;top:55px;width:979px;height:73px;background:#fff;border-radius:40px;box-shadow:0 2px 8px rgba(0,0,0,.08)}
.nav a{position:absolute;top:27px;font-size:14px;color:var(--ink);text-decoration:none}
.nav .active{color:var(--purple);font-weight:700}
.nav .active::after{content:"";position:absolute;left:0;right:0;top:34px;height:3px;background:var(--purple)}
.logo-disc{left:523px;top:14px;width:154px;height:154px;border-radius:50%;background:#fff;display:flex;flex-direction:column;align-items:center;justify-content:center;gap:8px}
.logo-dot{width:34px;height:34px;border-radius:50%;background:var(--purple)}
.logo-name{font-family:"Lato",sans-serif;font-weight:700;font-size:17px;letter-spacing:2px;color:var(--purple)}
.hero-title{left:115px;top:198px;font-family:"Righteous",sans-serif;font-size:56px;line-height:66px;color:#fff;text-shadow:2px 3px 4px rgba(40,20,70,.55);letter-spacing:1px}
.hero-sub{left:118px;top:410px;font-size:19px;color:#fff}

/* collections */
.coll{top:739px;width:385px;height:407px}
.coll h3{position:absolute;left:40px;top:38px;font-family:"Josefin Sans",sans-serif;font-weight:700;font-size:34px;color:var(--purple)}
.coll span{position:absolute;left:42px;top:92px;font-family:"Josefin Sans",sans-serif;font-weight:700;font-size:20px;text-decoration:underline;color:var(--ink)}

/* coming soon */
.circle{width:236px;height:236px;border-radius:50%}
.clabel{font-family:"Josefin Sans",sans-serif;font-size:24px;width:236px;text-align:center}
.small{font-size:12.5px;line-height:31px;color:var(--text)}

/* products */
.card{top:2481px;width:298px;height:361px;background:#fff;box-shadow:0 2px 10px rgba(0,0,0,.1)}
.card .img{position:absolute;left:0;top:0;width:298px;height:200px}
.card .name{position:absolute;left:28px;top:248px;font-size:19px}
.card .price{position:absolute;left:204px;top:246px;font-size:18px;font-weight:700;color:var(--purple)}
.card .btn{left:14px;top:294px;width:140px;height:42px;font-size:14px}
.arrow{width:34px;height:34px;border-radius:50%;display:flex;align-items:center;justify-content:center}

/* testimonials */
.tname{font-size:17px;font-weight:700}
.stars{color:#f4b400;font-size:15px;letter-spacing:1px}
.tbody{font-size:13px;line-height:28px;color:var(--text);width:440px;text-align:justify}
.avatar{width:80px;height:80px;border-radius:50%;background:linear-gradient(135deg,#e8e2dc,#b89a86)}

/* footer */
.footer{left:0;top:4305px;width:1200px;height:390px;background:var(--lavender-soft)}
.fh{font-size:17px;font-weight:700}
.flist{font-size:13px;line-height:23px;color:#333;list-style:none}
.flist2{font-size:13px;line-height:32px;color:#333;list-style:none}
.ficon{width:26px;height:26px;border-radius:5px;background:var(--purple);display:flex;align-items:center;justify-content:center}
.social{width:26px;height:26px;border-radius:50%;background:#cbbfd6}
.pay{width:34px;height:20px;border-radius:3px;background:#d9d3df}
</style>
</head>
<body>

<!-- Hero -->
<section>
  <div class="photo hero" role="img" aria-label="Lavender candles, lavender sprigs and oil bottle on a wooden table"></div>
  <nav class="abs nav">
    <a class="active" style="left:22px">Home</a>
    <a style="left:90px">About Us</a>
    <a style="left:177px">Products</a>
    <a style="left:261px">Testimonials</a>
    <a style="left:597px">Blog</a>
    <a style="left:650px">Shop</a>
    <svg class="abs" style="left:757px;top:26px" width="22" height="22" viewBox="0 0 24 24" fill="none" stroke="#222" stroke-width="2"><path d="M2 3h3l3 12h11l2-8H6"/><circle cx="9" cy="20" r="1.5"/><circle cx="18" cy="20" r="1.5"/></svg>
    <svg class="abs" style="left:793px;top:26px" width="20" height="20" viewBox="0 0 24 24" fill="none" stroke="#222" stroke-width="2.4"><circle cx="10" cy="10" r="7"/><path d="M15 15l7 7"/></svg>
    <div class="btn" style="left:832px;top:10px;width:138px;height:50px;font-size:15px">CONTACT US</div>
  </nav>
  <div class="abs logo-disc"><div class="logo-dot"></div><div class="logo-name">VELQUINT</div></div>
  <h1 class="abs hero-title">Elevate Your Choices<br>in Aromatherapy<br>Products</h1>
  <p class="abs hero-sub">Transform Your Space with the Warmth of Candlelight</p>
  <div class="btn" style="left:111px;top:456px;width:123px;height:48px">SHOP NOW</div>
</section>

<!-- Collections -->
<section>
  <div class="abs coll" style="left:0;background:radial-gradient(ellipse 130px 120px at 210px 300px,rgba(255,255,255,.9),rgba(255,255,255,0)),radial-gradient(ellipse 140px 60px at 80px 360px,rgba(110,100,150,.55),rgba(110,100,150,0)),linear-gradient(180deg,#e9e6ec 0%,#dcd7dd 55%,#b9b3b8 100%)" role="img" aria-label="White candles with lavender"><h3>Spring Collections</h3><span>Shop Now</span></div>
  <div class="abs coll" style="left:407px;background:radial-gradient(ellipse 120px 110px at 220px 320px,rgba(95,90,100,.75),rgba(95,90,100,0)),radial-gradient(ellipse 90px 80px at 70px 340px,rgba(130,125,115,.6),rgba(130,125,115,0)),linear-gradient(180deg,#e4e0e7 0%,#d3cfd6 55%,#aaa4ab 100%)" role="img" aria-label="Grey candles with reed diffuser"><h3>Autumn Story</h3><span>Shop Now</span></div>
  <div class="abs coll" style="left:815px;background:radial-gradient(ellipse 130px 120px at 190px 270px,rgba(245,236,215,.95),rgba(245,236,215,0)),radial-gradient(ellipse 100px 90px at 360px 200px,rgba(110,120,80,.45),rgba(110,120,80,0)),linear-gradient(180deg,#ede6de 0%,#ddd0be 55%,#bfa98e 100%)" role="img" aria-label="Cream candle with stones and leaves"><h3>Gift Of Nature</h3><span>Shop Now</span></div>
</section>

<!-- Coming soon -->
<section>
  <h2 class="abs hd hl" style="left:113px;top:1236px;font-size:42px">Coming Soon....</h2>
  <p class="abs hd" style="left:111px;top:1298px;font-size:25px;line-height:36px">The Scent of Happiness<br>is Coming!"</p>
  <p class="abs small" style="left:111px;top:1380px;width:240px">We're preparing something magical. Our carefully curated collection of luxurious candles will soon be ready to fill your space with warmth, scent, and serenity.</p>
  <div class="btn" style="left:114px;top:1558px;width:124px;height:48px">View All</div>
  <div class="abs circle" style="left:402px;top:1297px;background:radial-gradient(circle at 60% 45%,#f3ede4 0%,#dcc8b0 40%,#b08d6c 100%)" role="img" aria-label="Lotion bottles"></div>
  <div class="abs circle" style="left:661px;top:1297px;background:radial-gradient(circle at 50% 55%,#faf6ee 0%,#e6dccb 45%,#a89a86 100%)" role="img" aria-label="Handmade soaps with lavender"></div>
  <div class="abs circle" style="left:920px;top:1297px;background:radial-gradient(circle at 55% 50%,#a37c5a 0%,#c9dbc9 35%,#a8c3ac 100%)" role="img" aria-label="Body spray bottle"></div>
  <p class="abs clabel" style="left:402px;top:1552px">lotions</p>
  <p class="abs clabel" style="left:661px;top:1560px">Soaps</p>
  <p class="abs clabel" style="left:920px;top:1552px">Body Sprays</p>
</section>

<!-- About -->
<section>
  <div class="photo" style="left:0;top:1693px;width:562px;height:545px;background:radial-gradient(circle 130px at 240px 340px,#fff6c9 0%,#f3c84a 35%,rgba(230,200,150,.3) 70%,rgba(230,200,150,0)),linear-gradient(135deg,#ddd7d1,#cdbfb2 55%,#b9a493)" role="img" aria-label="Hands holding a lit candle"></div>
  <div class="abs" style="left:562px;top:1693px;width:638px;height:545px;background:var(--lavender)"></div>
  <h2 class="abs hd" style="left:642px;top:1745px;font-size:44px;font-weight:400">About <span class="hl">Us</span></h2>
  <p class="abs small" style="left:642px;top:1808px;width:445px;font-size:13px;line-height:33px">At Velquint, we believe that the simple flicker of a candle can transform any space into a sanctuary. We're a passionate team of candle lovers dedicated to creating high-quality, hand-poured candles that bring warmth, ambiance, and delightful scents to your home.<br>Each candle is thoughtfully crafted with eco-friendly materials, from the finest soy wax to carefully selected fragrances. Whether you're seeking a soothing lavender to unwind after a long day or a refreshing citrus scent to energize your mornings, we have something to elevate every moment.</p>
  <div class="btn" style="left:645px;top:2122px;width:125px;height:47px">READ MORE</div>
</section>

<!-- Products -->
<section>
  <h2 class="abs hd" style="left:0;top:2318px;width:1200px;text-align:center;font-size:42px;font-weight:400">Our <span class="hl">Products</span></h2>
  <p class="abs hd" style="left:0;top:2390px;width:1200px;text-align:center;font-size:24px;color:var(--purple)">Eco-Friendly Candles for a Sustainable Future</p>
  <div class="abs arrow" style="left:40px;top:2634px;background:var(--purple)"><svg width="12" height="12" viewBox="0 0 12 12"><path d="M8 2L4 6l4 4" stroke="#fff" stroke-width="2" fill="none"/></svg></div>
  <div class="abs arrow" style="left:1123px;top:2634px;background:#e6e6e6"><svg width="12" height="12" viewBox="0 0 12 12"><path d="M4 2l4 4-4 4" stroke="#fff" stroke-width="2" fill="none"/></svg></div>
  <div class="abs card" style="left:111px"><div class="img" style="background:radial-gradient(ellipse 70px 60px at 150px 110px,#f5efe3 0%,#e9e1d3 60%,rgba(233,225,211,0)),linear-gradient(180deg,#fafafa,#ededeb)" role="img" aria-label="Sandalwood candle in glass"></div><span class="name">Sandalwood</span><span class="price">$15.00</span><div class="btn">ADD TO CART</div></div>
  <div class="abs card" style="left:451px"><div class="img" style="background:radial-gradient(ellipse 140px 60px at 130px 120px,#8d5fd0,rgba(141,95,208,0)),linear-gradient(180deg,#3d3550 0%,#6e5a8c 35%,#9a7fc9 60%,#5b3c8a 85%,#e9e7ea 100%)" role="img" aria-label="Purple lavender candles"></div>
    <div class="abs" style="left:248px;top:14px;width:38px;height:74px;background:#fff;border-radius:4px"></div>
    <svg class="abs" style="left:257px;top:22px" width="20" height="18" viewBox="0 0 24 22"><path d="M12 21S2 14 2 7a5 5 0 0110-1 5 5 0 0110 1c0 7-10 14-10 14z" fill="#c4161c"/></svg>
    <svg class="abs" style="left:256px;top:56px" width="22" height="20" viewBox="0 0 24 24" fill="none" stroke="#222" stroke-width="2"><path d="M2 3h3l3 12h11l2-8H6"/><circle cx="9" cy="20" r="1.5"/><circle cx="18" cy="20" r="1.5"/></svg>
    <span class="name">Lavender Candle</span><span class="price" style="left:211px">$34.00</span><div class="btn" style="width:146px">SHOP NOW</div></div>
  <div class="abs card" style="left:790px"><div class="img" style="background:radial-gradient(ellipse 90px 70px at 130px 115px,#f0a888 0%,#f6cdb6 55%,rgba(246,205,182,0)),linear-gradient(180deg,#fbfaf9,#f4ece6)" role="img" aria-label="Peach hibiscus candles with towel and flower"></div><span class="name">Hibiscus candles</span><span class="price" style="left:203px">$15.00</span><div class="btn">ADD TO CART</div></div>
</section>

<!-- Custom candle -->
<section>
  <div class="photo" style="left:0;top:2931px;width:383px;height:476px;background:radial-gradient(ellipse 150px 170px at 170px 210px,#b386e8 0%,#7a3fc4 45%,rgba(80,40,130,0) 80%),linear-gradient(160deg,#3a2160,#5b2f96 45%,#2f3a2c 85%,#4a4f36)" role="img" aria-label="Purple candle in glass with lavender and rosemary"></div>
  <div class="abs" style="left:383px;top:2931px;width:443px;height:476px;background:var(--grey-band)"></div>
  <div class="photo" style="left:826px;top:2931px;width:374px;height:476px;background:radial-gradient(ellipse 110px 100px at 160px 320px,#fff5de 0%,#eadfd0 50%,rgba(234,223,208,0)),radial-gradient(ellipse 90px 110px at 80px 120px,#4a2c1c,rgba(74,44,28,0)),linear-gradient(180deg,#6d5a4d 0%,#a39283 40%,#ddd6cf 75%,#eeeae6 100%)" role="img" aria-label="Amber bottles and white candles on marble"></div>
  <h2 class="abs hd" style="left:383px;top:2985px;width:443px;text-align:center;font-size:44px;line-height:52px;font-weight:400">Create Your<br><span class="hl">Custom Candle</span></h2>
  <p class="abs small" style="left:413px;top:3121px;width:383px;text-align:center;font-size:12.5px">we're excited to offer custom candles that are completely tailored to you. Whether you're celebrating a special occasion, searching for a unique gift, or simply want a scent and design that's all your own, we've got you covered.</p>
  <div class="btn" style="left:518px;top:3275px;width:164px;height:46px">CUSTOMIZE HERE</div>
</section>

<!-- Testimonials -->
<section>
  <h2 class="abs hd" style="left:112px;top:3490px;font-size:44px;font-weight:400">Client <span class="hl">Testimonials</span></h2>
  <div class="abs arrow" style="left:1012px;top:3496px;background:var(--purple)"><svg width="12" height="12" viewBox="0 0 12 12"><path d="M8 2L4 6l4 4" stroke="#fff" stroke-width="2" fill="none"/></svg></div>
  <div class="abs arrow" style="left:1054px;top:3496px;background:#e6e6e6"><svg width="12" height="12" viewBox="0 0 12 12"><path d="M4 2l4 4-4 4" stroke="#fff" stroke-width="2" fill="none"/></svg></div>

  <div class="abs avatar" style="left:111px;top:3593px" role="img" aria-label="Client portrait"></div>
  <p class="abs tname" style="left:210px;top:3610px">Marisol Dane</p>
  <p class="abs stars" style="left:210px;top:3634px">★★★★★</p>
  <p class="abs tbody" style="left:111px;top:3688px">Lorem ipsum dolor sit amet, consectetur adipiscing elit, sed do eiusmod tempor incididunt ut labore et dolore magna aliqua. Ut enim ad minim veniam, quis nostrud exercitation ullamco laboris nisi ut aliquip ex ea commodo consequat.</p>
  <div class="abs" style="left:597px;top:3640px;width:4px;height:125px;background:#d6d6d6"></div>
  <div class="abs avatar" style="left:643px;top:3593px;background:linear-gradient(135deg,#f0e4dc,#d67a45)" role="img" aria-label="Client portrait"></div>
  <p class="abs tname" style="left:742px;top:3610px">Tavia Brook</p>
  <p class="abs stars" style="left:742px;top:3634px">★★★★★</p>
  <p class="abs tbody" style="left:642px;top:3688px">Lorem ipsum dolor sit amet, consectetur adipiscing elit, sed do eiusmod tempor incididunt ut labore et dolore magna aliqua. Ut enim ad minim veniam, quis nostrud exercitation ullamco laboris nisi ut aliquip ex ea commodo consequat.</p>
</section>

<!-- Newsletter -->
<section>
  <div class="photo" style="left:0;top:3880px;width:1200px;height:425px;background:radial-gradient(circle 60px at 1090px 60px,#f6dcb4,rgba(246,220,180,0)),radial-gradient(circle 60px at 950px 175px,#f6dcb4,rgba(246,220,180,0)),radial-gradient(circle 60px at 1045px 335px,#f6dcb4,rgba(246,220,180,0)),radial-gradient(ellipse 240px 200px at 900px 230px,rgba(120,80,190,.45),rgba(120,80,190,0)),linear-gradient(90deg,#d2d8dc 0%,#dde1e3 45%,#e6e6ea 70%,#ededee 100%)" role="img" aria-label="Tea light candles and lavender on a white textured surface"></div>
  <h2 class="abs hd" style="left:111px;top:3930px;font-size:42px;line-height:55px;font-weight:400">Subscribe To<br><span class="hl">Our Newsletter</span></h2>
  <p class="abs" style="left:108px;top:4060px;font-size:21px;color:#444">Join our list and get 15% off your first purchase!</p>
  <div class="abs" style="left:111px;top:4114px;width:490px;height:64px;background:#fff;border-radius:34px;font-size:14px;padding:24px 42px;color:#333">Enter Email Address</div>
  <div class="btn" style="left:112px;top:4199px;width:124px;height:48px">SUBSCRIBE</div>
</section>

<!-- Footer -->
<footer>
  <div class="abs footer"></div>
  <div class="abs" style="left:148px;top:4380px;width:200px;display:flex;flex-direction:column;align-items:center;gap:10px"><div class="logo-dot" style="width:48px;height:48px"></div><div class="logo-name" style="font-size:20px">VELQUINT</div></div>
  <div class="abs" style="left:177px;top:4596px;display:flex;gap:10px"><div class="social" style="background:var(--purple)"></div><div class="social"></div><div class="social"></div><div class="social"></div></div>

  <p class="abs fh" style="left:487px;top:4393px">Quick Links</p>
  <ul class="abs flist" style="left:489px;top:4425px"><li>Home</li><li>Shop</li><li>About Us</li><li>Products</li><li>Testimonials</li><li>Blog</li><li>Contact Us</li></ul>
  <p class="abs fh" style="left:642px;top:4393px">Other Links</p>
  <ul class="abs flist2" style="left:642px;top:4424px"><li>Support Center</li><li>Delivery &amp; Returns</li><li>Terms &amp; Conditions</li><li>Products Return</li><li>Wholesale Policy</li></ul>
  <p class="abs fh" style="left:876px;top:4391px">Contact Info</p>
  <div class="abs ficon" style="left:877px;top:4428px"><svg width="14" height="16" viewBox="0 0 14 18"><path d="M7 1a6 6 0 00-6 6c0 4 6 10 6 10s6-6 6-10a6 6 0 00-6-6z" fill="#fff"/><circle cx="7" cy="7" r="2" fill="#6b2fbf"/></svg></div>
  <p class="abs" style="left:920px;top:4434px;font-size:13px">Lorem Ipsum ,USA -437916</p>
  <div class="abs ficon" style="left:877px;top:4480px"><svg width="14" height="14" viewBox="0 0 24 24"><path d="M6 2l4 4-2 3a12 12 0 007 7l3-2 4 4-3 4C10 22 2 14 2 5z" fill="#fff"/></svg></div>
  <p class="abs" style="left:920px;top:4487px;font-size:13px">+1 888 888 88888</p>
  <div class="abs ficon" style="left:877px;top:4528px"><svg width="14" height="12" viewBox="0 0 24 18"><rect x="1" y="1" width="22" height="16" rx="2" fill="#fff"/><path d="M2 2l10 8 10-8" stroke="#6b2fbf" stroke-width="2" fill="none"/></svg></div>
  <p class="abs" style="left:922px;top:4535px;font-size:13px">info@velquint.com</p>

  <div class="abs" style="left:111px;top:4651px;width:979px;height:1px;background:#6b2fbf"></div>
  <div class="abs" style="left:105px;top:4662px;display:flex;gap:6px"><div class="pay"></div><div class="pay"></div><div class="pay"></div><div class="pay"></div><div class="pay"></div><div class="pay"></div><div class="pay"></div><span style="font-size:12px;font-weight:700;color:#333;margin-left:4px;line-height:20px">vonk</span></div>
  <p class="abs" style="left:832px;top:4665px;font-size:12.5px;color:#333">© 2025Velquint.All Rights Reserved</p>
</footer>

</body>
</html>
```